$5 Quest Website Required

I am looking for someone to develop a website akin to the simplicity of www.boxlantern.example with a video in the center or a tab that permits one to "Accept the Challenge."

Incorporates our logo and is used to promote our "$5 Quest Program."

Please see attachments, but we are igniting entrepreneurial spirit among our nation's youth through this interactive and intensive program!

There should be a way to navigate to other sections of the site including:

About
Why
Request $5 Quest Packet
Success Stories
Partners
Link to Norvik Holdings
Updates

Thanks to all in advance!

Looking forward to working with you!

Good feel of what we are looking for in terms of "feel"

http://www.thebrightripple.example/

Thank you,

RB

Please make note of this website, we are going for a feel that is akin to this and less modern and professional...more abstract and interactive...but of course include space for our video:

Colors, feel, imagery, is great. Keep your formats, but bring on the feel!

Thank you all for your hard work and patience.

Thank you all for your hard work thus far.

Meanwhile, please understand that the $5 Quest is young, youthful, full of challenge and vitality, it is a competition among students from high school and universities.  The websites you have delivered are too corporate, stale, and standard.  I'm looking for something that is fresh, different, like www.thebrightripple.example.

Symbols, cartoonish, but serious, down to business and save the world one $5 bill at a time.  The logo can be used as a theme...the colors, the feel.

Video space for explanation on the $5 Quest front and center.  With leaves, $ signs, colorful colors, etc.

Visual needs to be compelling to Join the Challenge! Although Norvik Holdings and the tree is a parent company; $5 Quest is separate and Norvik Holdings should only be mentioned as a link.

PixelHarbor.example in regard to simplicity; and www.thebrightripple.example in terms of style.

Thank you,

Raphael

Like the designs that have been submitted; we are almost there.

Target Market(s)

Professors, students, teachers, parents and NGO leaders who wish to use our program as a way to inspire leadership/entrepreneurship/fundraise for their causes.

Requirements
Must have
• Place for the video, front and center
Include logo
Forsight for blogging, message, etc.
Nice to have
• Plan "buckets" to include"
Explanation Video
Two pamphlets
Contract
FAQs
Website with Blog, voting, registration, video upload, etc.
Flyer perfected
Parable...symbol of our life
Photos
Stats included
Testimonials
Organizations that have used (TKWLM, North Brook Lodge, Marlowton High)
Sponsors (Open Lantern, Copperleaf Learningfield)
Photos from events

I understand this takes coding and such, but want you to be aware of the long term vision for it!

```html
<!DOCTYPE html>
<html lang="en">
<head>
<meta charset="utf-8">
<title>$5 Quest</title>
<link href="https://fonts.googleapis.com/css2?family=Arimo:wght@400;700&family=Questrial&display=swap" rel="stylesheet">
<style>
:root{
  --green:#1f9a3e;
  --green-dark:#17722e;
  --green-head:#1c6b2a;
  --leaf:#7cc242;
  --grey-logo:#6b6b6b;
  --text:#8a8a8a;
  --text-dark:#333;
  --page:#e4e4e4;
  --panel:#d2d2d2;
  --nav:#5a5a5a;
  --white:#ffffff;
  --link:#1a5fa8;
}
*{margin:0;padding:0;box-sizing:border-box}
html,body{width:841px;height:1200px;overflow:hidden}
body{position:relative;background:var(--page);font-family:"Questrial",sans-serif;color:var(--text)}
a{text-decoration:none}
.abs{position:absolute}
.hero-bg{left:0;top:0;width:841px;height:600px;background:linear-gradient(#f7f7f7,#ececec)}
.brand{left:60px;top:18px;display:flex;align-items:center;gap:10px}
.brand-mark{width:118px;height:118px;border-radius:50%;background:var(--leaf)}
.brand-name{font-family:"Arimo",sans-serif;font-weight:700;font-size:62px;color:var(--grey-logo);letter-spacing:-1px}
.account{right:50px;top:18px;font-family:"Arimo",sans-serif;font-size:11px;text-align:right}
.account a{color:var(--link);margin-left:14px}
.account .lang{display:block;color:var(--text-dark);margin-top:9px}
.portrait{left:560px;top:226px;width:281px;height:367px;background:linear-gradient(160deg,#c9a88a,#e7e9ee 45%,#b8c8dc)}
.video{left:193px;top:176px;width:370px;height:371px;background:var(--white);border:1px solid #bbb;box-shadow:0 2px 6px rgba(0,0,0,.25);padding:3px}
.video-still{width:100%;height:350px;background:linear-gradient(135deg,#efefef,#d8d8d8 60%,#cfc4bb)}
.play{left:141px;top:148px;width:82px;height:82px;border-radius:50%;background:#222}
.play svg{display:block}
.video-bar{left:3px;bottom:3px;right:3px;height:18px;background:#1e1e1e;display:flex;align-items:center;gap:6px;padding:0 5px;font-family:"Arimo",sans-serif;font-size:9px;color:#fff}
.video-bar .track{flex:1;height:6px;background:#777}
.video-bar .track i{display:block;width:16%;height:100%;background:#ddd}
.crowd{left:0;top:593px;width:841px;height:50px;background:linear-gradient(90deg,#c7b8b4,#d8cfcd,#c4b8b8,#d6cbc8)}
.nav{left:51px;top:600px;width:738px;height:37px;background:var(--nav);display:flex;align-items:center;justify-content:center;font-family:"Arimo",sans-serif;font-weight:700;font-size:12px}
.nav a{color:var(--white);padding:0 14px;border-left:1px solid #999}
.nav a:first-child{border-left:0}
.panel{background:var(--panel);box-shadow:0 1px 3px rgba(0,0,0,.2)}
.panel h2{font-family:"Arimo",sans-serif;font-weight:700;font-size:19px;color:var(--green-head)}
.portfolio{left:51px;top:664px;width:493px;height:369px;padding:16px 18px}
.portfolio-copy{margin-top:10px;font-size:9.4px;line-height:17.7px}
.portfolio-copy span{display:block;white-space:nowrap;overflow:hidden}
.portfolio-copy a{color:var(--text-dark);font-size:10px}
.accept{left:76px;top:978px;width:248px;height:36px;background:linear-gradient(#2fa84a,var(--green-dark));color:var(--white);font-family:"Arimo",sans-serif;font-weight:700;font-size:16px;letter-spacing:.5px;display:flex;align-items:center;justify-content:center;border-radius:2px}
.social{left:341px;top:982px;display:flex;gap:10px}
.social span{width:28px;height:28px;border-radius:50%;background:#2f5b9a}
.social span:nth-child(2){background:#3aa3dd}
.social span:nth-child(3){background:#4a7fc4}
.social span:nth-child(4){background:#f2f2f2;border:1px solid #bbb}
.social span:nth-child(5){background:#2867b2}
.side{left:567px;top:664px;width:229px;height:369px;padding:16px 10px}
.quote{font-size:9.6px;line-height:16px;margin-top:10px;padding:0 4px;white-space:nowrap;overflow:hidden}
.quote cite{display:block;text-align:right;font-style:normal;color:var(--text-dark);margin-top:2px}
.side hr{border:0;border-top:1px solid #bbb;margin:10px 0}
.faq h3{font-family:"Arimo",sans-serif;font-size:11.5px;color:var(--text-dark);margin:14px 4px 4px}
.faq p{font-size:9.6px;line-height:16px;padding:0 4px;white-space:nowrap;overflow:hidden}
.actions{left:67px;top:1060px;display:flex}
.action{height:36px;background:linear-gradient(#fdfdfd,#dcdcdc);border:1px solid #bdbdbd;font-family:"Arimo",sans-serif;font-weight:700;font-size:13px;color:var(--text-dark);display:flex;align-items:center;padding-left:40px;position:relative;margin-right:15px}
.action i{position:absolute;left:3px;top:-6px;width:30px;height:30px;border-radius:50%}
.footer{left:0;top:1110px;width:841px;height:30px}
.footer-band{left:0;top:1126px;width:841px;height:74px;background:var(--green)}
.footer-links{left:56px;top:1143px;font-family:"Arimo",sans-serif;font-size:10px;color:var(--white)}
.footer-links a{color:var(--white)}
.sponsors{right:88px;top:1143px;font-family:"Arimo",sans-serif;font-size:10px;color:var(--white);text-decoration:underline}
.copy{left:56px;top:1173px;font-family:"Arimo",sans-serif;font-size:10px;color:var(--white)}
</style>
</head>
<body>
<div class="abs hero-bg"></div>

<div class="abs brand">
  <span class="brand-mark"></span>
  <span class="brand-name">$5 Quest</span>
</div>

<div class="abs account">
  <a href="#">Sign In</a><a href="#">Sign Up</a>
  <span class="lang">English ▾</span>
</div>

<div class="abs portrait" role="img" aria-label="Photo of a smiling young woman writing on a glass board with a marker"></div>

<div class="abs video">
  <div class="video-still" role="img" aria-label="Video still: hand-drawn mind map with Success in the centre linked to Teamwork, Innovation, Vision, Leadership and Motivation"></div>
  <div class="abs play">
    <svg width="82" height="82" viewBox="0 0 82 82"><path d="M32 24 L60 41 L32 58 Z" fill="#fff"/></svg>
  </div>
  <div class="abs video-bar">
    <span>❚❚</span><span>00:12</span>
    <span class="track"><i></i></span>
    <span>✕</span>
  </div>
</div>

<div class="abs crowd" role="img" aria-label="Faded photo strip of cheering students"></div>
<nav class="abs nav">
  <a href="#">About</a><a href="#">Why</a><a href="#">Request $5 Quest Packet</a><a href="#">Success Stories</a><a href="#">Partners</a><a href="#">Link to Norvik Holdings</a>
</nav>

<section class="abs panel portfolio">
  <h2>Portfolio Managment</h2>
  <div class="portfolio-copy">
    <span>school and student entrepreneurship organizations across the country and challenging students</span>
    <span>to put their entrepreneurial genius to work in rder to multiply their "$5 eX Factor" as many</span>
    <span>A recent phenomenon, lead by social enterprise Norvik Holdings in collaboration with Copperleaf</span>
    <span>Learningfield and Halden University, called "The 5 Dollar Quest" is sweeping across high</span>
    <span>school and student entrepreneurship organizations across the country and challenging students</span>
    <span>to put their entrepreneurial genius to work in rder to multiply their "$5 eX Factor" as many</span>
    <span>A recent phenomenon, lead by social enterprise Norvik Holdings in collaboration with Copperleaf</span>
    <span>Learningfield and Halden University, called "The 5 Dollar Quest" is sweeping across high</span>
    <span>school and student entrepreneurship organizations across the country and challenging students</span>
    <span>to put their entrepreneurial genius to work in rder to multiply their "$5 eX Factor" as many</span>
    <span>A recent phenomenon, lead by social enterprise Norvik Holdings in collaboration with Copperleaf</span>
    <span>Learningfield and Halden University, called "The 5 Dollar Quest" is sweeping across high</span>
    <span>school and student entrepreneurship organizations across the country and challenging students</span>
    <span>to put their entrepreneurial genius to work in rder to multiply their "$5 eX Factor" <a href="#">Read More...</a></span>
  </div>
</section>
<a class="abs accept" href="#">ACCEPT THE CHALLENGE</a>
<div class="abs social"><span></span><span></span><span></span><span></span><span></span></div>

<aside class="abs panel side">
  <h2>Testimonial</h2>
  <div class="quote">A recent phenomenon, lead by social<br>Norvik Holdings in collaboration with Cop<br>Learningfield<cite>- Owen Marsh</cite></div>
  <div class="quote">A recent phenomenon, lead by social<br>Norvik Holdings in collaboration with Cop<br>Learningfield<cite>- Owen Marsh</cite></div>
  <hr>
  <h2>FAQs</h2>
  <div class="faq">
    <h3>Are You Ready for 5 $ Quest?</h3>
    <p>A recent phenomenon, lead by social</p>
    <p>A recent phenomenon, lead by social</p>
    <h3>Are You Ready for 5 $ Quest?</h3>
    <p>A recent phenomenon, lead by social fa</p>
    <p>A recent phenomenon, lead by social fa</p>
  </div>
</aside>

<div class="abs actions">
  <a class="action" href="#" style="width:138px"><i style="background:#c62828"></i>Upload Video</a>
  <a class="action" href="#" style="width:180px"><i style="background:#e0a030"></i>Upload Event Photo</a>
  <a class="action" href="#" style="width:180px"><i style="background:#5aac2a"></i>Download Pamphlets</a>
  <a class="action" href="#" style="width:164px"><i style="background:#2f6fc0"></i>Contact Us</a>
</div>

<svg class="abs footer" width="841" height="30" viewBox="0 0 841 30" aria-hidden="true">
  <path d="M0 18 L20 10 L38 16 L60 8 L85 15 L110 6 L140 14 L170 9 L200 16 L230 7 L262 14 L295 9 L330 16 L360 6 L395 13 L430 8 L465 15 L500 7 L535 14 L570 9 L605 16 L640 6 L675 13 L710 8 L745 15 L780 7 L812 14 L841 9 L841 30 L0 30 Z" fill="var(--green)"/>
</svg>
<div class="abs footer-band"></div>
<div class="abs footer-links"><a href="#">About</a> | <a href="#">Why</a> | <a href="#">Request $5 Quest Packet</a> | <a href="#">Success Stories</a> | <a href="#">Patners</a> | <a href="#">Link to Norvik Holdings</a></div>
<div class="abs sponsors">Sponsors ▾</div>
<div class="abs copy">© Copyright 2005 5 $ Quest | Privacy Policy</div>
</body>
</html>
```